Brightfield Ventures Inc. Letterhead

Creation of attractive and eye catching letterhead for a business start-up for the construction industry. Letterhead must relate to construction, but avoid standard hammer and tools in the design.

I forgot to add some details, sorry about that. Some pertinent info: Ph: 916-555-0187 brightfieldventures.example 448 Willowmere Ave, Ste 210 Folsom, CA 95999 info@brightfieldventures.example not sure if slogan should be in there" “Connecting construction professionals to create a purpose driven industry.” must be able to be used in word. Thanks!

```html
<!DOCTYPE html>
<html lang="en">
<head>
<meta charset="UTF-8">
<title>Brightfield Ventures Inc. Letterhead</title>
<link href="https://fonts.googleapis.com/css2?family=Open+Sans:wght@400;600;700&display=swap" rel="stylesheet">
<style>
  :root {
    --brand-red: #c0080b;
    --brand-navy: #1b1f5a;
    --ink: #2b2b2b;
    --muted: #555a66;
    --backdrop: #e9eaec;
    --paper: #ffffff;
  }
  * { margin: 0; padding: 0; box-sizing: border-box; }
  html, body {
    width: 1200px; height: 784px; overflow: hidden;
    background: var(--backdrop);
    font-family: "Open Sans", Arial, sans-serif;
  }
  .letterhead {
    position: absolute; left: 340px; top: 24px;
    width: 520px; height: 736px;
    background: var(--paper);
    box-shadow: 0 2px 10px rgba(0,0,0,0.12);
    overflow: hidden;
  }
  .brand {
    position: absolute; left: 48px; top: 44px;
    display: flex; align-items: center; gap: 7px;
  }
  .brand-square { width: 14px; height: 14px; background: var(--brand-red); }
  .brand-name {
    font-size: 11px; font-weight: 700; letter-spacing: 1.6px;
    color: var(--brand-navy); text-transform: uppercase;
  }
  .contact {
    position: absolute; right: 48px; top: 38px;
    border-left: 1px solid var(--muted);
    padding-left: 7px;
    font-style: normal;
    font-size: 6.5px; line-height: 10px; color: var(--muted);
  }
  .contact-line { display: flex; align-items: center; gap: 4px; }
  .contact-icon { width: 6px; height: 6px; fill: var(--brand-red); flex: none; }
  .letter-body {
    position: absolute; left: 60px; top: 120px; width: 390px;
    font-size: 8.6px; line-height: 12.5px; color: var(--ink);
  }
  .salutation { font-size: 11px; font-weight: 700; margin-bottom: 14px; }
  .letter-body p { margin-bottom: 14px; }
  .signature {
    display: block; width: 120px; height: 42px; margin-top: 4px;
    background: linear-gradient(90deg, #f1f1f3, #e2e3e7);
    border-radius: 3px;
  }
  .footer-wave { position: absolute; left: 0; bottom: 0; width: 520px; height: 170px; }
  .footer-url {
    position: absolute; left: 40px; bottom: 26px;
    font-size: 9.5px; letter-spacing: 1.2px; color: #fff;
  }
</style>
</head>
<body>
  <main class="letterhead">
    <header>
      <div class="brand">
        <span class="brand-square"></span>
        <span class="brand-name">Brightfield Ventures</span>
      </div>
      <address class="contact">
        <div>448 Willowmere Ave, Ste 210</div>
        <div>Folsom, CA 95999</div>
        <div class="contact-line">
          <svg class="contact-icon" viewBox="0 0 10 10"><path d="M2 0.5 L4 2.8 L3 4 Q4.2 6 6 7 L7.2 6 L9.5 8 L8 9.5 Q3.5 9 0.5 2 Z"/></svg>
          <span>Ph: 916-555-0187</span>
        </div>
        <div class="contact-line">
          <svg class="contact-icon" viewBox="0 0 10 10"><rect x="0" y="1.5" width="10" height="7"/></svg>
          <span>info@brightfieldventures.example</span>
        </div>
      </address>
    </header>

    <section class="letter-body">
      <div class="salutation">Dear Mr. Dalton,</div>
      <p>Lorem Ipsum is simply dummy text of the printing and typesetting industry. Lorem Ipsum has been the industry’s standard dummy text ever since the 1500s, when an unknown printer took a galley of type and scrambled it to make a type specimen book. It has survived not only five centuries, but also the leap into electronic typesetting, remaining essentially unchanged.</p>
      <p>The standard chunk of Lorem Ipsum used since the 1500s is reproduced below for those interested. Sections 1.10.32 and 1.10.33 from the original treatise are also reproduced in their exact original form, accompanied by English versions from a later translation that is still in wide use by printers today.</p>
      <p>Lorem Ipsum is simply dummy text of the printing and typesetting industry. Lorem Ipsum has been the industry’s standard dummy text ever since the 1500s, when an unknown printer took a galley of type and scrambled it to make a type specimen book. It has survived not only five centuries, but also the leap into electronic typesetting, remaining essentially unchanged. It was popularised in the</p>
      <p>Lorem Ipsum is simply dummy text of the printing and typesetting industry. Lorem Ipsum has been the industry’s standard dummy text ever since the 1500s, when an unknown printer took a galley of type and scrambled it to make a type specimen book. It has survived not only five centuries, but also the leap into electronic typesetting, remaining essentially unchanged. It was popularised in the</p>
      <span class="signature" role="img" aria-label="Handwritten signature of the sender"></span>
    </section>

    <footer>
      <svg class="footer-wave" viewBox="0 0 520 170" preserveAspectRatio="none" aria-hidden="true">
        <path d="M0 70 C150 60 300 150 520 10 L520 18 C300 158 150 68 0 78 Z" fill="var(--brand-red)"/>
        <path d="M0 82 C150 72 300 162 520 24 L520 34 C300 172 150 82 0 92 Z" fill="var(--brand-navy)"/>
        <path d="M0 97 C150 87 300 177 520 40 L520 170 L0 170 Z" fill="var(--brand-red)"/>
      </svg>
      <div class="footer-url">www.brightfieldventures.example</div>
    </footer>
  </main>
</body>
</html>
```